New Corporate Email Signature with Custom GIF KAV Electric LLC & KAV Fire & Security

Project Overview
KAV Electric LLC and KAV Fire & Security are seeking a professional, polished, and technically robust corporate email signature design. The project has two integrated deliverables:
A custom animated GIF representing both sides of our business
A complete corporate email signature layout designed for real-world compatibility (Gmail, Outlook, iOS, Android)
Our brand aesthetic is corporate, conservative, and clean. We value clarity, trust, professionalism, and subtle creativity β€” nothing overly flashy or cartoonish.
This design will be used across the entire company and must be visually aligned with our brand while remaining technically dependable.

PART 1 β€” Animated GIF Requirements
The GIF will be the core visual anchor of the new signature.
It must be clean, smooth, subtle, and optimized for email use.
βš™ Technical Requirements
Max file size: 150–200 KB (smaller is better)
Dimensions: approx 300px width (flexible, but must look good small)
Looping: continuous loop
Style: professional, minimalistic transitions

No rapid flashing or harsh animations
Must export cleanly into a format email clients accept

🎞 GIF Animation Sequence
Phase 1 β€” KAV Electric (KE)
Use the yellow β€œKE” avatar logo (provided).
Animation flow:
KE avatar appears
Full name β€œKAV Electric LLC” slides in, fades in, or otherwise appears smoothly
A scrolling or cycling list of service offerings displays:
EV Charging Stations
Generator & Transformers
Testing & Troubleshooting
LED Lighting Upgrades
After the list is shown, the entire KE segment fades out

Phase 2 β€” KAV Fire & Security (KF)
Use the red β€œKF” avatar logo (provided).
Animation flow mirrors Phase 1:
KF avatar appears
Full name β€œKAV Fire & Security” slides/fades in
Scrolling or cycling list of services displays:
Fire Alarm Upgrades
BQTL 48 Test & Inspect
Security Surveillance Systems
Access Control Systems
Data & Fiber Optic Cabling
Fade out β†’ loop back to KE
Creative Direction

Designers are encouraged to use:
Clean transitions
Soft fades
Professional typography
Modern minimalism
Consistent brand colors
High clarity at small sizes

Avoid:
Busy motion
Hard flashes
Excessive text overlays
Overly long transitions

The goal: a smooth, corporate-grade rotation that fits seamlessly into an email signature.

PART 2 β€” Corporate Email Signature Design

The signature must be visually appealing, brand-aligned, and structurally bulletproof across all major email systems.
πŸ“ Required Elements
πŸ‘€ Left Side Content
Circular headshot (we will supply final photos)
Social media icons with embedded URLs:
Facebook
LinkedIn
Google Business Profile
Instagram

Icons should be clean, modern, and in alignment with brand colors
πŸ“„ Right Side Content
Name
Title
KAV Electric LLC / KAV Fire & Security (depending on user)
Phone number
Email address
License# 52804
Physical office address: 58 Larkspur Rd, Brookdale QX 40318

Small CTA for newsletter signup (button or micro-banner)

🏒 Branding Assets Provided

You will receive:
KE avatar logo
KF avatar logo
Full-name KE logo
Full-name KF logo

These should be incorporated naturally and professionally.

Design Requirements

Conservative corporate styling

Clean typography

Balanced use of white space

Professional hierarchy

Light and dark mode compatibility preferred

Layout should not rely on one large image

All images should export cleanly for hosting on servers/CDN

Avoid overly tall signatures

The final signature must present as modern, trustworthy, and technically reliable across platforms.

πŸ§ͺ Compatibility Requirements

The signature must display correctly in:

Gmail (web and mobile)

Outlook (desktop & online)

Apple Mail

iPhone Mail

Android mail apps

Designers must avoid DIV-based layouts and instead propose a layout that can be implemented using table-based HTML, which is the industry standard for email compatibility.

You do not need to build the HTML β€” only supply the final layered design (PSD/AI/Figma) plus a clear structural layout that can be converted to HTML later.

πŸ“¦ Deliverables
1. Animated GIF

Final optimized GIF

Source file (After Effects, Photoshop, or equivalent)

Export guidelines so we can reproduce future versions

2. Email Signature Design

Full static design mockup

Modular layout for each employee

Icon set for social media

Newsletter CTA element

Clear spacing, alignment, and typography specifications

All source files (PSD, AI, Figma, etc.)

🧭 Creative Guidance Summary

We want:
βœ” Modern
βœ” Corporate
βœ” Minimalistic
βœ” Professional
βœ” Clean motion
βœ” Consistent branding
βœ” Email-safe elements

We do not want:
✘ Flashy marketing look
✘ Overly colorful or playful styles
✘ Hard-to-read fonts
✘ Heavy animation
✘ Oversized signatures

πŸ›  Tools & Format Flexibility

We allow full creative freedom regarding:

Animation style

Typography choices

Structuring of the two-column layout

How the service lists scroll or cycle

As long as the end result is clean, brand-aligned, professional, and email-compatible.

πŸ’¬ Final Note to Designers

We encourage creativity within the boundaries of corporate professionalism.
This signature will represent our company every time an email is sent β€” it must communicate trust, clarity, expertise, and brand strength.

```html
<!DOCTYPE html>
<html lang="en">
<head>
<meta charset="utf-8">
<title>KAV Email Signatures</title>
<link rel="stylesheet" href="https://fonts.googleapis.com/css2?family=Poppins:wght@400;500;600;700&display=swap">
<style>
  :root {
    --page-bg: #b8b8b8;
    --card-bg: #ffffff;
    --electric: #e6cd17;
    --fire: #d42228;
    --ink: #262626;
    --ink-soft: #3a3a3a;
    --brand-grey: #5a5a5a;
    --cta-bg: #2a2a2a;
    --rule: #3a3a3a;
    --ring-edge: #d6d6d6;
  }
  * { box-sizing: border-box; margin: 0; padding: 0; }
  html, body {
    width: 1200px; height: 560px; overflow: hidden;
    background: var(--page-bg);
    font-family: "Poppins", Arial, sans-serif;
    color: var(--ink);
  }
  .icon-sprite { position: absolute; width: 0; height: 0; }

  .signature {
    position: absolute; left: 24px;
    width: 1120px; height: 256px;
    background: var(--card-bg);
    overflow: hidden;
  }
  .signature--electric { top: 16px; --accent: var(--electric); --cta-text: var(--electric); --icon: var(--ink); --license: var(--ink); --brand-color: var(--brand-grey); }
  .signature--fire { top: 288px; --accent: var(--fire); --cta-text: #ffffff; --icon: var(--fire); --license: #ffffff; --brand-color: var(--fire); }

  .signature__shapes { position: absolute; inset: 0; width: 1120px; height: 256px; }
  .shape-accent { fill: var(--accent); }
  .shape-cta { fill: var(--cta-bg); }
  .shape-ring { fill: #ffffff; }
  .shape-ring-edge { fill: none; stroke: var(--ring-edge); stroke-width: 1; }
  .shape-social { fill: #ffffff; }

  .signature__name {
    position: absolute; left: 293px; top: 20px;
    font-size: 32px; font-weight: 600; line-height: 1.2; color: var(--ink);
  }
  .signature__title {
    position: absolute; left: 294px; top: 64px;
    font-size: 18px; font-weight: 400; color: var(--ink-soft);
  }
  .signature__brand {
    position: absolute; left: 294px; top: 146px;
    display: flex; align-items: center; gap: 14px;
  }
  .brand__dot { width: 30px; height: 30px; border-radius: 50%; background: var(--accent); flex: none; }
  .brand__name {
    font-size: 28px; font-weight: 600; letter-spacing: 0.5px; white-space: nowrap;
    color: var(--brand-color);
  }

  .signature__divider {
    position: absolute; left: 731px; top: 24px;
    width: 2px; height: 176px; background: var(--rule);
  }
  .contact { position: absolute; left: 768px; top: 36px; list-style: none; }
  .contact__item {
    display: flex; align-items: flex-start; gap: 16px;
    font-size: 20px; line-height: 30px; color: var(--ink);
    margin-bottom: 14px; white-space: nowrap;
  }
  .contact__icon { width: 22px; height: 22px; margin-top: 4px; color: var(--icon); fill: currentColor; flex: none; }

  .signature__license {
    position: absolute; left: 288px; top: 219px;
    font-size: 22px; font-weight: 600; line-height: 32px; color: var(--license);
  }
  .signature__cta {
    position: absolute; left: 874px; top: 219px;
    font-size: 21px; font-weight: 600; line-height: 32px; color: var(--cta-text);
  }
</style>
</head>
<body>

<svg class="icon-sprite" aria-hidden="true">
  <symbol id="icon-pin" viewBox="0 0 24 24"><path d="M12 1.5a7.5 7.5 0 0 0-7.5 7.5c0 5.6 7.5 13.5 7.5 13.5s7.5-7.9 7.5-13.5A7.5 7.5 0 0 0 12 1.5zm0 10.3a2.8 2.8 0 1 1 0-5.6 2.8 2.8 0 0 1 0 5.6z"/></symbol>
  <symbol id="icon-phone" viewBox="0 0 24 24"><path d="M6.6 10.8a15.2 15.2 0 0 0 6.6 6.6l2.2-2.2c.3-.3.7-.4 1-.2 1.1.4 2.3.6 3.6.6.6 0 1 .4 1 1V20c0 .6-.4 1-1 1A17 17 0 0 1 3 4c0-.6.4-1 1-1h3.5c.6 0 1 .4 1 1 0 1.3.2 2.5.6 3.6.1.3 0 .7-.2 1z"/></symbol>
  <symbol id="icon-mail" viewBox="0 0 24 24"><path d="M2 5h20v14H2z"/><path d="M2 5l10 7 10-7" fill="none" stroke="#fff" stroke-width="2"/></symbol>
  <defs>
    <linearGradient id="photoTone" x1="0" y1="0" x2="0" y2="1">
      <stop offset="0" stop-color="#d9d9d9"/><stop offset="1" stop-color="#6f7378"/>
    </linearGradient>
  </defs>
</svg>

<section class="signature signature--electric" aria-label="KAV Electric LLC email signature">
  <svg class="signature__shapes" viewBox="0 0 700 160">
    <path class="shape-accent" d="M0 0 H150 Q168 0 168 18 V100 Q168 135 200 135 H540 L525 160 H0 Z"/>
    <path class="shape-cta" d="M540 135 H700 V160 H525 Z"/>
    <circle class="shape-ring" cx="113" cy="78" r="63"/>
    <circle class="shape-ring-edge" cx="113" cy="78" r="53"/>
    <circle cx="113" cy="78" r="51" fill="url(#photoTone)" role="img" aria-label="Circular employee headshot"/>
    <g class="social-links">
      <circle class="shape-social" cx="25" cy="30" r="13" role="img" aria-label="Social profile link 1"/>
      <circle class="shape-social" cx="25" cy="64" r="13" role="img" aria-label="Social profile link 2"/>
      <circle class="shape-social" cx="25" cy="98" r="13" role="img" aria-label="Social profile link 3"/>
      <circle class="shape-social" cx="25" cy="132" r="13" role="img" aria-label="Social profile link 4"/>
    </g>
  </svg>

  <h1 class="signature__name">Alex Marlow</h1>
  <p class="signature__title">Director</p>
  <div class="signature__brand"><span class="brand__dot"></span><span class="brand__name">KAV Electric LLC</span></div>

  <div class="signature__divider"></div>
  <ul class="contact">
    <li class="contact__item"><svg class="contact__icon"><use href="#icon-pin"/></svg><span>58 Larkspur Rd,<br>Brookdale QX 40318</span></li>
    <li class="contact__item"><svg class="contact__icon"><use href="#icon-phone"/></svg><span>+1-555-014-2290</span></li>
    <li class="contact__item"><svg class="contact__icon"><use href="#icon-mail"/></svg><span>info@kavmail.com</span></li>
  </ul>

  <p class="signature__license">License# 52804</p>
  <p class="signature__cta">Join Our Newsletter</p>
</section>

<section class="signature signature--fire" aria-label="KAV Fire &amp; Security email signature">
  <svg class="signature__shapes" viewBox="0 0 700 160">
    <path class="shape-accent" d="M0 0 H150 Q168 0 168 18 V100 Q168 135 200 135 H540 L525 160 H0 Z"/>
    <path class="shape-cta" d="M540 135 H700 V160 H525 Z"/>
    <circle class="shape-ring" cx="113" cy="78" r="63"/>
    <circle class="shape-ring-edge" cx="113" cy="78" r="53"/>
    <circle cx="113" cy="78" r="51" fill="url(#photoTone)" role="img" aria-label="Circular employee headshot"/>
    <g class="social-links">
      <circle class="shape-social" cx="25" cy="30" r="13" role="img" aria-label="Social profile link 1"/>
      <circle class="shape-social" cx="25" cy="64" r="13" role="img" aria-label="Social profile link 2"/>
      <circle class="shape-social" cx="25" cy="98" r="13" role="img" aria-label="Social profile link 3"/>
      <circle class="shape-social" cx="25" cy="132" r="13" role="img" aria-label="Social profile link 4"/>
    </g>
  </svg>

  <h1 class="signature__name">Alex Marlow</h1>
  <p class="signature__title">Director</p>
  <div class="signature__brand"><span class="brand__dot"></span><span class="brand__name">KAV Fire &amp; Security</span></div>

  <div class="signature__divider"></div>
  <ul class="contact">
    <li class="contact__item"><svg class="contact__icon"><use href="#icon-pin"/></svg><span>58 Larkspur Rd,<br>Brookdale QX 40318</span></li>
    <li class="contact__item"><svg class="contact__icon"><use href="#icon-phone"/></svg><span>+1-555-014-2290</span></li>
    <li class="contact__item"><svg class="contact__icon"><use href="#icon-mail"/></svg><span>info@kavmail.com</span></li>
  </ul>

  <p class="signature__license">License# 52804</p>
  <p class="signature__cta">Join Our Newsletter</p>
</section>

</body>
</html>
```